Packaging Design for Vanta Prime

We require an outstanding packaging design for our Vanta Prime brand, which offers hydration electrolyte supplements specifically tailored for athletes and sporty individuals.

Benchmark packaging design from quellix competitor attached. The product packaging contains 20 x 20g sticks of the product.

Target Market

Psychographic: Health-conscious, active lifestyle, values quality, functionality and sustainability.

product description 1:
HYDRATION BOOSTER
Refresh, Replenish, Recharge!

product description 2:
PREMIUM ISOTONIC ELECTROLYTE DRINK
Nutritional Expertise Since 1992.

Existing Logo: to add "since 1992"

Appeal to Target Market: Create a design that resonates with both men and women in the 25-55 age group.

Grafik Design: Develop a visually striking design that grabs attention in online retail environments like Brindleport.

Visuals: glass of water (or symbolic) and sticks (powder) just like benchmark brand quellix.

Design Elements
Use colours that are inside the Vanta-Prime Logo, attached.
Product will be available in 3 flavours. Lemon=yellow, Orange=orange, Black Currant=purple

Typography: Utilize strong, clean, and modern fonts. Ensure readability and create a sense of strength, endurance and reliability.

The product will be available in 3 flavours: Lemon, Orange and Johannisbeere

We look forward to seeing your creative ideas and innovative designs for our Vanta Prime brand packaging.

```html
<!DOCTYPE html>
<html lang="en">
<head>
<meta charset="utf-8">
<title>Vanta Prime Hydration Booster – Flavour Range</title>
<link rel="stylesheet" href="https://fonts.googleapis.com/css2?family=Roboto+Condensed:wght@700&family=Audiowide&display=swap">
<style>
  :root {
    --stage-light: #7f9ef0;
    --stage-dark: #2a4bb8;
    --pouch-blue: #1f4fb5;
    --pouch-blue-deep: #163c94;
    --brand-yellow: #f2de12;
    --brand-magenta: #c2185b;
    --text-white: #ffffff;
    --seal-dark: #2b2b2b;
    --seal-gold: #e2a43a;
    --orange: #f26a0f;
    --lemon: #f3e61c;
    --currant: #5b1c8c;
  }
  * { box-sizing: border-box; margin: 0; padding: 0; }
  html, body { width: 1200px; height: 600px; overflow: hidden; }
  body {
    background: radial-gradient(ellipse at 50% 35%, var(--stage-light) 0%, #5b7fe0 45%, var(--stage-dark) 100%);
    font-family: "Roboto Condensed", "Arial Narrow", sans-serif;
    position: relative;
  }
  .range { position: absolute; inset: 0; }
  .pouch {
    position: absolute; top: 87px; width: 306px; height: 428px;
    background: linear-gradient(160deg, #2b5fc8 0%, var(--pouch-blue) 45%, var(--pouch-blue-deep) 100%);
    overflow: hidden;
  }
  .pouch--orange { left: 68px; --flavour: var(--orange); --band-text: var(--text-white); --count-bg: var(--brand-yellow); --count-text: #111; }
  .pouch--lemon { left: 429px; --flavour: var(--lemon); --band-text: #111; --count-bg: #c8102e; --count-text: #fff; }
  .pouch--currant { left: 790px; --flavour: var(--currant); --band-text: var(--text-white); --count-bg: #ffffff; --count-text: #222; }

  .pouch__band {
    position: absolute; top: 0; left: 0; right: 0; height: 39px;
    background: var(--flavour); color: var(--band-text);
    font-size: 13.5px; text-align: center; line-height: 44px; letter-spacing: 0.1px;
  }
  .pouch__brand {
    position: absolute; top: 110px; left: 0; right: 0; text-align: center;
    color: var(--brand-yellow); font-size: 38px; line-height: 1;
  }
  .pouch__brand-dot {
    display: inline-block; width: 18px; height: 18px; border-radius: 50%;
    background: var(--brand-yellow); margin-right: 8px; vertical-align: 4px;
  }
  .pouch__title {
    position: absolute; left: 0; right: 0; text-align: center;
    font-family: "Audiowide", "Roboto Condensed", sans-serif; line-height: 1;
  }
  .pouch__title--hydration { top: 200px; color: var(--text-white); font-size: 30px; }
  .pouch__title--booster { top: 242px; color: var(--brand-yellow); font-size: 33px; }

  .pouch__claims { position: absolute; top: 287px; left: 48px; list-style: none; color: var(--text-white); font-size: 14.5px; }
  .pouch__claims li { height: 25px; }
  .pouch__claims li::before { content: "•"; font-size: 9px; margin-right: 5px; vertical-align: 3px; }

  .seal {
    position: absolute; top: 322px; left: 138px; width: 40px; height: 40px; border-radius: 50%;
    background: var(--seal-dark); border: 2px solid var(--seal-gold);
    color: #fff; text-align: center; transform: rotate(-14deg);
    display: flex; flex-direction: column; justify-content: center; line-height: 1;
  }
  .seal__small { font-size: 7px; }
  .seal__year { font-size: 12px; }

  .serve-visual {
    position: absolute; top: 262px; left: 206px; width: 78px; height: 138px;
    background: linear-gradient(175deg, rgba(255,255,255,0.05) 0%, rgba(170,200,240,0.35) 40%, var(--flavour) 100%);
    border-radius: 4px 4px 10px 10px;
  }
  .serve-visual__flavour {
    position: absolute; top: 310px; left: 200px; width: 100px; text-align: center;
    color: var(--flavour); font-size: 10px;
  }
  .pouch--lemon .serve-visual__flavour { color: #1a2f7a; }
  .pouch--currant .serve-visual__flavour { color: #e8e8f5; }
  .count {
    position: absolute; top: 347px; left: 232px; width: 30px; height: 30px; border-radius: 50%;
    background: var(--count-bg); color: var(--count-text);
    text-align: center; line-height: 1; display: flex; flex-direction: column; justify-content: center;
  }
  .count__num { font-size: 13px; }
  .count__unit { font-size: 4.5px; }

  .pouch__base { position: absolute; left: 0; bottom: 0; width: 306px; height: 70px; }
  .badges { position: absolute; top: 386px; left: 48px; display: flex; gap: 12px; align-items: flex-start; }
  .badge { display: flex; flex-direction: column; align-items: center; gap: 3px; }
  .badge__shape { width: 20px; height: 20px; border-radius: 50%; border: 1.5px solid rgba(255,255,255,0.8); }
  .badge__shape--square { width: 30px; height: 26px; border-radius: 2px; background: rgba(255,255,255,0.85); border: none; }
  .badge__label { font-size: 4.5px; color: #fff; }
  .pouch__weight {
    position: absolute; bottom: 0; left: 0; right: 0; text-align: center;
    color: var(--text-white); font-size: 11px; line-height: 18px;
  }
  .pouch--lemon .pouch__weight { color: #111; }
</style>
</head>
<body>
<main class="range">

  <section class="pouch pouch--orange">
    <div class="pouch__band">PREMIUM ISOTONIC ELECTROLYTE DRINK</div>
    <div class="pouch__brand"><span class="pouch__brand-dot"></span>Vanta Prime</div>
    <h2 class="pouch__title pouch__title--hydration">HYDRATION</h2>
    <h3 class="pouch__title pouch__title--booster">BOOSTER</h3>
    <ul class="pouch__claims"><li>REFRESH</li><li>REPLENISH</li><li>RECHARGE!</li></ul>
    <div class="seal"><span class="seal__small">Since</span><span class="seal__year">1992</span></div>
    <div class="serve-visual" role="img" aria-label="Glass of water with orange powder pouring from a stick"></div>
    <div class="serve-visual__flavour">Orange Flavor</div>
    <div class="count"><span class="count__num">20</span><span class="count__unit">STICKS</span></div>
    <svg class="pouch__base" viewBox="0 0 306 70" preserveAspectRatio="none" aria-hidden="true">
      <path d="M0 50 C90 48 200 40 306 0 L306 70 L0 70 Z" fill="var(--flavour)"/>
    </svg>
    <div class="badges">
      <div class="badge"><span class="badge__shape badge__shape--square"></span></div>
      <div class="badge"><span class="badge__shape"></span><span class="badge__label">VEGAN</span></div>
      <div class="badge"><span class="badge__shape"></span><span class="badge__label">GLUTENFREI</span></div>
      <div class="badge"><span class="badge__shape"></span><span class="badge__label">LAKTOSEFREI</span></div>
    </div>
    <div class="pouch__weight">Net Wt. 400g</div>
  </section>

  <section class="pouch pouch--lemon">
    <div class="pouch__band">PREMIUM ISOTONIC ELECTROLYTE DRINK</div>
    <div class="pouch__brand"><span class="pouch__brand-dot"></span>Vanta Prime</div>
    <h2 class="pouch__title pouch__title--hydration">HYDRATION</h2>
    <h3 class="pouch__title pouch__title--booster">BOOSTER</h3>
    <ul class="pouch__claims"><li>REFRESH</li><li>REPLENISH</li><li>RECHARGE!</li></ul>
    <div class="seal"><span class="seal__small">Since</span><span class="seal__year">1992</span></div>
    <div class="serve-visual" role="img" aria-label="Glass of water with lemon powder pouring from a stick"></div>
    <div class="serve-visual__flavour">Lemon Flavor</div>
    <div class="count"><span class="count__num">20</span><span class="count__unit">STICKS</span></div>
    <svg class="pouch__base" viewBox="0 0 306 70" preserveAspectRatio="none" aria-hidden="true">
      <path d="M0 50 C90 48 200 40 306 0 L306 70 L0 70 Z" fill="var(--flavour)"/>
    </svg>
    <div class="badges">
      <div class="badge"><span class="badge__shape badge__shape--square"></span></div>
      <div class="badge"><span class="badge__shape"></span><span class="badge__label">VEGAN</span></div>
      <div class="badge"><span class="badge__shape"></span><span class="badge__label">GLUTENFREI</span></div>
      <div class="badge"><span class="badge__shape"></span><span class="badge__label">LAKTOSEFREI</span></div>
    </div>
    <div class="pouch__weight">Net Wt. 400g</div>
  </section>

  <section class="pouch pouch--currant">
    <div class="pouch__band">PREMIUM ISOTONIC ELECTROLYTE DRINK</div>
    <div class="pouch__brand"><span class="pouch__brand-dot"></span>Vanta Prime</div>
    <h2 class="pouch__title pouch__title--hydration">HYDRATION</h2>
    <h3 class="pouch__title pouch__title--booster">BOOSTER</h3>
    <ul class="pouch__claims"><li>REFRESH</li><li>REPLENISH</li><li>RECHARGE!</li></ul>
    <div class="seal"><span class="seal__small">Since</span><span class="seal__year">1992</span></div>
    <div class="serve-visual" role="img" aria-label="Glass of water with black currant powder pouring from a stick"></div>
    <div class="serve-visual__flavour">Black Currant Flavor</div>
    <div class="count"><span class="count__num">20</span><span class="count__unit">STICKS</span></div>
    <svg class="pouch__base" viewBox="0 0 306 70" preserveAspectRatio="none" aria-hidden="true">
      <path d="M0 50 C90 48 200 40 306 0 L306 70 L0 70 Z" fill="var(--flavour)"/>
    </svg>
    <div class="badges">
      <div class="badge"><span class="badge__shape badge__shape--square"></span></div>
      <div class="badge"><span class="badge__shape"></span><span class="badge__label">VEGAN</span></div>
      <div class="badge"><span class="badge__shape"></span><span class="badge__label">GLUTENFREI</span></div>
      <div class="badge"><span class="badge__shape"></span><span class="badge__label">LAKTOSEFREI</span></div>
    </div>
    <div class="pouch__weight">Net Wt. 400g</div>
  </section>

</main>
</body>
</html>
```